New web design for a service provider in the medical field

We are looking for a new design for our website. We are a company that repairs and sells medical endoscopes. Our customers include doctors and hospitals. Our current website can be found at https://lumavex.de/en/lumavex-english.
We need a new web design (without programming) for the following 3 pages:
-Startpage https://lumavex.de/en/lumavex-english/
-Used endoscopes https://lumavex.de/en/used-endoscopes/
-Purchase https://lumavex.de/en/purchase/
The design should be modern and stylish.
The blue color of the logo should be reflected on the page, but not too intrusive.
I have uploaded the images from the header. If more images are needed, let me know and I will upload them.

Target Market(s)
Doctors and hospitals

```html
<!DOCTYPE html>
<html lang="en">
<head>
<meta charset="utf-8">
<title>Lumavex – Endoscope Repair &amp; Sale</title>
<link rel="stylesheet" href="https://fonts.googleapis.com/css2?family=Questrial&family=Montserrat:wght@400;500;600;700&display=swap">
<style>
:root{
  --blue:#1a9ad6;
  --blue-btn:#1f98d8;
  --blue-deep:#136da3;
  --blue-band:#1874aa;
  --ink:#1d1f24;
  --text:#5b6066;
  --muted:#8a8f95;
  --light:#f3f5f8;
  --footer:#1d2228;
  --white:#ffffff;
}
*{box-sizing:border-box;margin:0;padding:0}
html,body{width:1200px;height:4428px;overflow:hidden}
body{font-family:"Montserrat",sans-serif;color:var(--text);background:var(--white);position:relative}
h1,h2,h3,h4{font-family:"Questrial",sans-serif;font-weight:400;color:var(--ink)}
.container{width:940px;margin:0 auto;position:relative}
.btn{display:inline-block;background:var(--blue-btn);color:var(--white);font-size:10px;font-weight:600;letter-spacing:.5px;text-transform:uppercase;padding:0 28px;height:30px;line-height:30px;text-decoration:none}
.section{position:absolute;left:0;width:1200px}

/* top bar */
.topbar{top:0;height:21px;background:var(--blue);color:var(--white);font-size:9px}
.topbar .container{display:flex;justify-content:space-between;align-items:center;height:21px}
.topbar span{margin-right:14px}
.topbar .right span{margin:0 0 0 22px}

/* nav */
.nav{top:21px;height:60px;background:var(--white)}
.nav .container{display:flex;justify-content:space-between;align-items:center;height:60px}
.brand{display:flex;align-items:center;gap:8px;font-family:"Montserrat",sans-serif;font-weight:700;font-size:15px;color:#1f3d5a}
.brand-dot{width:10px;height:10px;border-radius:50%;background:var(--blue)}
.menu{display:flex;gap:32px;font-size:9px;font-weight:500;color:#2a2d33}
.menu .active{color:var(--blue)}

/* hero */
.hero{top:81px;height:486px;overflow:hidden}
.hero-photo{position:absolute;inset:0;background:linear-gradient(100deg,#cfd3d8 0%,#eceef0 40%,#f4f5f6 70%,#e4e7ea 100%)}
.hero-text{position:absolute;left:776px;top:152px}
.hero-text .pre{font-family:"Questrial",sans-serif;font-size:20px;color:var(--ink)}
.hero-text h1{font-size:40px;line-height:48px;margin:10px 0 20px}
.hero-wave{position:absolute;left:0;bottom:0}

/* welcome */
.welcome{top:636px;height:344px}
.welcome .text{position:absolute;left:130px;top:56px;width:450px}
.pre{font-family:"Questrial",sans-serif;font-size:14px;color:var(--ink)}
.welcome h2{font-size:32px;margin:6px 0 20px}
.welcome p{font-size:11.5px;line-height:19px;margin-bottom:30px}
.welcome .photo{position:absolute;left:648px;top:0;width:422px;height:344px;border-radius:4px 4px 40px 4px;background:linear-gradient(135deg,#d9dde1,#f2f3f4 55%,#c7ccd2)}

/* blue intro */
.intro{top:1049px;height:450px;background:var(--blue-deep);overflow:hidden}
.intro .text{position:absolute;left:130px;top:74px;width:430px;color:var(--white)}
.intro .pre{color:var(--white);font-size:14px}
.intro h2{color:var(--white);font-size:34px;line-height:38px;margin:6px 0 14px}
.intro .tag{font-size:14px;text-transform:uppercase;font-family:"Questrial",sans-serif}
.intro p{font-size:11.5px;line-height:20px;margin:28px 0 30px}
.intro svg{position:absolute;right:0;top:0}

/* service cards */
.services{top:1568px;height:240px}
.services .grid{display:flex;gap:20px}
.card{width:300px;height:240px;text-align:center;padding:14px 20px 0;background:var(--white)}
.card.outline{border:1px solid #5a5f66}
.card.raised{box-shadow:0 2px 14px rgba(0,0,0,.12)}
.card svg{display:block;margin:0 auto 6px}
.card h3{font-size:16px}
.card .sub{color:var(--blue);font-size:11px;margin:2px 0 16px}
.card p{font-size:9.5px;line-height:16px;height:52px;margin-bottom:10px}
.card .btn{height:30px;padding:0 22px}

/* decision timeline */
.decision{top:1877px;height:744px;background:var(--light)}
.decision .head{text-align:center;padding-top:50px}
.decision .head h2{font-size:32px;margin-top:6px}
.timeline{position:absolute;left:0;top:0;width:1200px;height:744px}
.timeline .line{position:absolute;left:599px;top:187px;width:2px;height:470px;background:var(--blue)}
.node{position:absolute;left:571px;width:58px;height:58px;border-radius:50%;border:2px solid var(--blue);background:var(--white);display:flex;align-items:center;justify-content:center}
.item{position:absolute;width:395px}
.item.left{left:135px;text-align:right}
.item.right{left:670px}
.item h4{font-size:15px;margin-bottom:8px}
.item p{font-size:9.5px;line-height:17px}

/* contact */
.contact{top:2621px;height:435px;background:linear-gradient(180deg,#1a6ea1,#18679b);color:var(--white)}
.contact .head{text-align:center;padding-top:58px}
.contact .pre{color:var(--white);font-size:13px}
.contact h2{color:var(--white);font-size:32px;margin-top:4px}
.form{position:absolute;left:286px;top:142px;width:628px}
.field{position:absolute;border-bottom:1px solid rgba(255,255,255,.7);height:22px;font-size:10px;font-weight:600}
.submit{position:absolute;left:226px;top:248px;width:176px;height:40px;background:var(--white);color:var(--ink);font-size:10px;font-weight:700;text-align:center;line-height:40px}

/* outcome */
.outcome{top:3077px;height:700px}
.outcome .head{text-align:center;padding-top:52px}
.outcome h2{font-size:32px;margin-top:4px}
.features{position:absolute;left:0;top:130px;width:1200px}
.feature{position:absolute;width:280px;text-align:center}
.feature .circle{width:118px;height:118px;border-radius:50%;background:var(--blue);margin:0 auto 18px;display:flex;align-items:center;justify-content:center;box-shadow:inset 0 0 0 6px var(--blue),inset 0 0 0 8px rgba(255,255,255,.8)}
.feature h4{font-size:16px;margin-bottom:10px}
.feature p{font-size:10.5px;line-height:18px;padding:0 20px}
.makers{position:absolute;top:603px;left:384px;display:flex;gap:12px}
.maker{width:136px;height:40px;border-radius:12px 0 12px 0;color:var(--white);font-size:11px;font-weight:600;text-align:center;line-height:40px}
.maker.m1{background:#1769c9}.maker.m2{background:#d6214a}.maker.m3{background:#26282c}

/* faulty band */
.faulty{top:3773px;height:276px}
.faulty svg{position:absolute;top:0;left:0}
.faulty .text{position:absolute;top:78px;width:1200px;text-align:center;color:var(--white)}
.faulty h2{color:var(--white);font-size:32px}
.faulty .tag{font-size:15px;font-family:"Questrial",sans-serif;margin:12px 0 20px}
.faulty .btn{height:36px;line-height:36px}

/* footer */
.footer{top:4048px;height:380px;background:var(--footer);color:#c9ccd0;font-size:10px}
.footer .brand{position:absolute;left:144px;top:108px;color:var(--white);font-size:24px}
.footer .brand-dot{width:14px;height:14px}
.footer .about{position:absolute;left:130px;top:178px;width:230px;line-height:17px}
.social{position:absolute;left:130px;top:264px;display:flex;gap:14px}
.social span{width:36px;height:36px;border-radius:50%;border:2px solid var(--white)}
.fcol{position:absolute;top:74px}
.fcol h5{font-family:"Questrial",sans-serif;font-weight:400;font-size:15px;color:var(--blue);margin-bottom:16px}
.fcol li{list-style:none;margin-bottom:11px}
.crow{display:flex;gap:10px;align-items:flex-start;margin-bottom:18px;line-height:14px}
.crow .ic{width:24px;height:24px;border-radius:50%;background:var(--blue);flex:none;display:flex;align-items:center;justify-content:center}
.news input{display:block;width:220px;height:32px;border:0;padding:0 12px;font-size:10px;font-family:"Montserrat",sans-serif}
.news .btn{width:220px;text-align:center;margin-top:6px;height:32px;line-height:32px}
.copy{position:absolute;right:130px;top:288px;font-size:9px}
.copy b{color:var(--blue);font-weight:400}
</style>
</head>
<body>

<header class="section topbar">
  <div class="container">
    <div><span>PICK-UP ORDER</span><span>|</span><span>ABOUT US</span><span>|</span><span>CONTACT US</span></div>
    <div class="right"><span>☎ +49 4020 555 718-0</span><span>✉ info@lumavex.de</span><span>En ▾</span></div>
  </div>
</header>

<nav class="section nav">
  <div class="container">
    <div class="brand"><span class="brand-dot"></span>Lumavex</div>
    <div class="menu">
      <span class="active">HOME</span><span>ENDOSCOPE REPAIR</span><span>USED ENDOSCOPES</span><span>ENDOSCOPY SYSTEMS</span><span>ENDOSCOPY ACCESSORIES</span><span>PURCHASE</span>
    </div>
  </div>
</nav>

<section class="section hero">
  <div class="hero-photo" role="img" aria-label="Flexible endoscope control head held in a white stand"></div>
  <div class="hero-text">
    <div class="pre">Put Your</div>
    <h1>Endoscope In<br>Reliable Hands!</h1>
    <a class="btn">Get Started</a>
  </div>
  <svg class="hero-wave" width="1200" height="80" viewBox="0 0 1200 80">
    <path d="M0 60 C250 30 420 90 650 55 C850 25 1000 10 1200 60 L1200 80 L0 80Z" fill="var(--blue)"/>
    <path d="M0 72 C250 50 420 100 650 68 C850 40 1000 30 1200 72 L1200 80 L0 80Z" fill="var(--white)"/>
  </svg>
</section>

<section class="section welcome">
  <div class="text">
    <div class="pre">Welcome To</div>
    <h2>Lumavex</h2>
    <p>GmbH is specialized in repairing and saling flexible endoscopes along with accessories and consumables. We offer endoscopes, processors, light sources, accessories and much more – with a focus on the manufacturers Orvana, Pentiq and Fujara.</p>
    <a class="btn">About Us</a>
  </div>
  <div class="photo" role="img" aria-label="Video processor unit with touch display panel"></div>
</section>

<section class="section intro">
  <div class="text">
    <div class="pre">Endoscope repairs and</div>
    <h2>Second hand endoscopes from Lumavex</h2>
    <div class="tag">Cause the outcome matters!</div>
    <p>Lumavex is a privileged partner for the start-up facility or optimisation of existing healthcare facilities, doctor's offices and hospitals. The quality and reliability of our products and our offered service are our best advertisement!</p>
    <a class="btn">About Us</a>
  </div>
  <svg width="660" height="450" viewBox="0 0 660 450" role="img" aria-label="Row of flexible endoscopes lying side by side">
    <defs><linearGradient id="scopeTone" x1="0" y1="0" x2="1" y2="1"><stop offset="0" stop-color="#e9ebee"/><stop offset="1" stop-color="#c9ced4"/></linearGradient></defs>
    <path d="M660 0 L190 0 C100 60 80 200 40 300 C20 360 0 420 0 450 L660 450Z" fill="var(--white)"/>
    <path d="M660 0 L215 0 C125 60 105 200 65 300 C45 360 30 420 28 450 L660 450Z" fill="url(#scopeTone)"/>
  </svg>
</section>

<section class="section services">
  <div class="container grid">
    <div class="card outline">
      <svg width="44" height="44" viewBox="0 0 44 44" fill="none" stroke="#2a2d33" stroke-width="1.6"><circle cx="20" cy="18" r="12"/><circle cx="20" cy="18" r="6" stroke="var(--blue)"/><rect x="12" y="30" width="22" height="8" rx="3" stroke="var(--blue)"/></svg>
      <h3>Repair</h3><div class="sub">Endoscope repair service</div>
      <p>Manufacturer-independent we repair and maintain endoscopes, individual components (e.g. processors or light sources)...</p>
      <a class="btn">Repair Request</a>
    </div>
    <div class="card raised">
      <svg width="44" height="44" viewBox="0 0 44 44" fill="none" stroke="#2a2d33" stroke-width="1.6"><path d="M26 6 L38 18 L18 38 L6 26Z"/><circle cx="28" cy="14" r="3" stroke="var(--blue)"/><path d="M14 26 l6 -6" stroke="var(--blue)"/></svg>
      <h3>Sale</h3><div class="sub">Used endoscopes</div>
      <p>Our regular stock includes refurbished gastroscopes, coloscopes, bronchoscopes, cystoscopes...</p>
      <a class="btn">Purchase Request</a>
    </div>
    <div class="card outline">
      <svg width="44" height="44" viewBox="0 0 44 44" fill="none" stroke="#2a2d33" stroke-width="1.6"><rect x="8" y="14" width="22" height="24" rx="3"/><path d="M14 14 v-5 a5 5 0 0 1 10 0 v5"/><path d="M24 30 L36 18 L40 22 L28 34Z" stroke="var(--blue)"/></svg>
      <h3>Purchase</h3><div class="sub">Used endoscopes</div>
      <p>We are very interested in buying your old endoscopes – even defective and dismantled! We offer fair conditions! Please contact us...</p>
      <a class="btn">Sell Request</a>
    </div>
  </div>
</section>

<section class="section decision">
  <div class="head">
    <div class="pre">Lumavex GmbH</div>
    <h2>Your Decision for your Future</h2>
  </div>
  <div class="timeline">
    <div class="line"></div>
    <div class="node" style="top:158px"><svg width="26" height="26" viewBox="0 0 26 26" fill="none" stroke="var(--blue)" stroke-width="1.6"><circle cx="13" cy="13" r="7"/><circle cx="13" cy="13" r="2.5"/></svg></div>
    <div class="node" style="top:251px"><svg width="26" height="26" viewBox="0 0 26 26" fill="none" stroke="var(--blue)" stroke-width="1.6"><ellipse cx="11" cy="7" rx="7" ry="3"/><path d="M4 7v12c0 2 14 2 14 0V7"/><path d="M20 18 V6 m-3 3 l3-3 3 3"/></svg></div>
    <div class="node" style="top:346px"><svg width="26" height="26" viewBox="0 0 26 26" fill="none" stroke="var(--blue)" stroke-width="1.6"><circle cx="13" cy="13" r="9"/><path d="M13 7v6l4 3"/></svg></div>
    <div class="node" style="top:440px"><svg width="26" height="26" viewBox="0 0 26 26" fill="none" stroke="var(--blue)" stroke-width="1.6"><rect x="5" y="5" width="16" height="12" rx="2"/><path d="M3 21h20"/></svg></div>
    <div class="node" style="top:535px"><svg width="26" height="26" viewBox="0 0 26 26" fill="none" stroke="var(--blue)" stroke-width="1.6"><path d="M5 21 L15 11 M17 5 a5 5 0 0 0 4 7 l-3 -3Z M5 5 l16 16"/></svg></div>
    <div class="node" style="top:629px"><svg width="26" height="26" viewBox="0 0 26 26" fill="none" stroke="var(--blue)" stroke-width="1.6"><circle cx="13" cy="13" r="4"/><path d="M13 3v4M13 19v4M3 13h4M19 13h4M6 6l3 3M17 17l3 3M20 6l-3 3M9 17l-3 3"/></svg></div>

    <div class="item left" style="top:150px"><h4>Fast Repairs</h4><p>Keep potential disruptions in your doctor's office or in your hospital at minimum as a result of optimized processes and highly qualified specialists in our company</p></div>
    <div class="item right" style="top:244px"><h4>Highly cost Efficient</h4><p>Benefit from our first class recommendations and implementation by our experienced staff. Our goals is to find the best solutions together with you at the best lowest price point.</p></div>
    <div class="item left" style="top:338px"><h4>On-site service</h4><p>We will gladly pay you a visit to to carry out analysis and repairs on site. Due to our many years of experience – it doesn't get any faster (whigleithin a 250 km range)</p></div>
    <div class="item right" style="top:440px"><h4>Loan equipment service</h4><p>Use our service of high-quality loan devices during the downtime of your defective endoscope (limited to stock)</p></div>
    <div class="item left" style="top:533px"><h4>Without a maintenance contract</h4><p>No subscription or other maintenance contract, but one-time and sustainable repair work</p></div>
    <div class="item right" style="top:638px"><h4>First class Service</h4><p>Our clients always come first!</p></div>
  </div>
</section>

<section class="section contact">
  <div class="head">
    <div class="pre">Contact Us</div>
    <h2>How Can We help You?</h2>
  </div>
  <div class="form">
    <div class="field" style="left:0;top:0;width:306px">Name:</div>
    <div class="field" style="left:320px;top:0;width:308px">Phone:</div>
    <div class="field" style="left:0;top:55px;width:628px">Email:</div>
    <div class="field" style="left:0;top:110px;width:628px;height:74px">Comments:</div>
    <div class="submit">SUBMIT</div>
  </div>
</section>

<section class="section outcome">
  <div class="head">
    <div class="pre">Cause The</div>
    <h2>Outcome Matters!</h2>
  </div>
  <div class="features">
    <div class="feature" style="left:140px;top:0"><div class="circle"><svg width="50" height="50" viewBox="0 0 50 50" fill="none" stroke="#fff" stroke-width="2"><circle cx="17" cy="18" r="8"/><circle cx="33" cy="18" r="8"/><path d="M5 42c2-9 22-9 24 0M21 42c2-9 22-9 24 0"/></svg></div><h4>One Company For Everyone</h4><p>We are a service provider for doctors and hospitals!</p></div>
    <div class="feature" style="left:460px;top:0"><div class="circle"><svg width="50" height="50" viewBox="0 0 50 50" fill="none" stroke="#fff" stroke-width="2"><circle cx="25" cy="28" r="6"/><path d="M14 44c2-8 20-8 22 0"/><path d="M10 12l2 4 4 0-3 3 1 4-4-2-4 2 1-4-3-3 4 0Z M40 12l2 4 4 0-3 3 1 4-4-2-4 2 1-4-3-3 4 0Z M25 4l2 4 4 0-3 3 1 4-4-2-4 2 1-4-3-3 4 0Z"/></svg></div><h4>Experience Characterises Us</h4><p>We are a service provider for doctors and hospitals!</p></div>
    <div class="feature" style="left:780px;top:0"><div class="circle"><svg width="50" height="50" viewBox="0 0 50 50" fill="none" stroke="#fff" stroke-width="2"><rect x="7" y="8" width="36" height="26" rx="2"/><path d="M18 42h14M25 34v8"/><rect x="17" y="14" width="16" height="14"/></svg></div><h4>The Product Is Close To Our Hearts</h4><p>We are a service provider for doctors and hospitals!</p></div>
    <div class="feature" style="left:140px;top:228px"><div class="circle"><svg width="50" height="50" viewBox="0 0 50 50" fill="none" stroke="#fff" stroke-width="2"><circle cx="25" cy="20" r="13"/><path d="M19 20l4 4 8-8M17 31l-5 14 7-3 4 6 2-10M33 31l5 14-7-3-4 6"/></svg></div><h4>Guaranteed Service</h4><p>We are a service provider for doctors and hospitals!</p></div>
    <div class="feature" style="left:460px;top:228px"><div class="circle"><svg width="50" height="50" viewBox="0 0 50 50" fill="none" stroke="#fff" stroke-width="2"><circle cx="16" cy="30" r="10"/><circle cx="34" cy="20" r="10"/><path d="M11 30h10M16 25v10M29 20h10M25 4v8m-4-4l4 4 4-4"/></svg></div><h4>Quality Not Quantity</h4><p>We are a service provider for doctors and hospitals!</p></div>
    <div class="feature" style="left:780px;top:228px"><div class="circle"><svg width="50" height="50" viewBox="0 0 50 50" fill="none" stroke="#fff" stroke-width="2"><circle cx="25" cy="17" r="8"/><path d="M6 22v12l10 10h6M44 22v12L34 44h-6"/></svg></div><h4>Services For Everyone</h4><p>We are a service provider for doctors and hospitals!</p></div>
  </div>
  <div class="makers">
    <div class="maker m1">ORVANA</div>
    <div class="maker m2">PENTIQ</div>
    <div class="maker m3">FUJARA</div>
  </div>
</section>

<section class="section faulty">
  <svg width="1200" height="276" viewBox="0 0 1200 276">
    <path d="M0 20 C300 -10 500 60 800 30 C1000 10 1100 0 1200 15 L1200 276 L0 276Z" fill="var(--blue-band)"/>
  </svg>
  <div class="text">
    <h2>Faulty Endoscope?</h2>
    <div class="tag">WE ENSURE QUICK AND SMOOTH REPAIRS!</div>
    <a class="btn">Pick Up Order</a>
  </div>
</section>

<footer class="section footer">
  <div class="brand"><span class="brand-dot"></span>Lumavex</div>
  <p class="about">Lumavex GmbH is specialised in the repair and sale of Orvana, Pentiq and Fujara flexible medical endoscopes.</p>
  <div class="social"><span></span><span></span></div>

  <div class="fcol" style="left:430px">
    <h5>Quick Links</h5>
    <ul><li>Home</li><li>Endoscope Repair</li><li>Used Endoscopes</li><li>Endoscopy Systems</li><li>Endoscopy Accessories</li><li>Purchase</li></ul>
  </div>
  <div class="fcol" style="left:610px">
    <h5>Contacts</h5>
    <div class="crow"><span class="ic"><svg width="12" height="12" viewBox="0 0 12 12" fill="#fff"><path d="M6 0a4 4 0 0 1 4 4c0 3-4 8-4 8S2 7 2 4a4 4 0 0 1 4-4Z"/></svg></span><span>Lindenweg 12<br>21400 Brunsdorf, Germany</span></div>
    <div class="crow"><span class="ic"><svg width="12" height="12" viewBox="0 0 12 12" fill="#fff"><path d="M2 1l2.5 0 1 3-1.5 1c.7 1.5 1.5 2.3 3 3l1-1.5 3 1V11C5 11 1 7 1 2Z"/></svg></span><span style="padding-top:5px">+49 4020 555 718-0</span></div>
    <div class="crow"><span class="ic"><svg width="12" height="12" viewBox="0 0 12 12" fill="none" stroke="#fff"><rect x="1" y="2.5" width="10" height="7"/><path d="M1 2.5l5 4 5-4"/></svg></span><span style="padding-top:5px">info@lumavex.de</span></div>
  </div>
  <div class="fcol news" style="left:850px">
    <h5>Newsletter</h5>
    <input type="text" placeholder="Enter Your Email">
    <a class="btn">Subscribe</a>
  </div>
  <div class="copy">Copyright © 2022 <b>Lumavex</b>. All Rights Reserved.</div>
</footer>

</body>
</html>
```